Classy, Elegant, Simple Business Card Design

Looking to have a classy, simple, and elegant design. Want a top notch designed business card. I really like the look of the new torvane credit card. I also like the design I attached. I am trying to reach 21-29 year old females for booking us for there wedding or event. We offer Disc Jockey Service, Photo Booth Rentals, and Uplighting .

Target Market(s)

21-28 year old females

Contact Information for Business Card

Has to have logo, website, email, and phone number

Font styles to use
Other font styles liked:
• open to font choice, modern, clean
Designer to choose
33a6d7
0791cd
0555a3
ffffff

Requirements
Must have
• Has to have logo, website, email, and phone number
Nice to have
• I really like the design of the new torvane credit card. I also included my logo and some designs I like
Should not have
• clutter or too much info

```html
<!DOCTYPE html>
<html lang="en">
<head>
<meta charset="utf-8">
<title>Tidecrest Event Group – Business Card</title>
<link rel="stylesheet" href="https://fonts.googleapis.com/css2?family=Roboto:wght@400;500;700&display=swap">
<style>
  :root {
    --sky: #33a6d7;
    --azure: #0791cd;
    --royal: #0555a3;
    --navy: #1d3f73;
    --white: #ffffff;
    --card: #f4f5f6;
    --ink: #2b2f36;
    --stage: #c9c9c9;
  }
  * { box-sizing: border-box; margin: 0; padding: 0; }
  html, body { width: 1200px; height: 576px; overflow: hidden; }
  body {
    background: var(--stage);
    font-family: "Roboto", Arial, sans-serif;
    position: relative;
  }
  .card {
    position: absolute;
    width: 484px;
    height: 294px;
    border-radius: 10px;
    background: var(--card);
    overflow: hidden;
  }
  .card--front { left: 82px; top: 140px; }
  .card--back { left: 602px; top: 138px; }

  .brand {
    position: absolute;
    text-align: center;
    color: var(--royal);
    font-weight: 500;
  }
  .brand__mark {
    display: block;
    width: 46px; height: 46px;
    margin: 0 auto 10px;
    border-radius: 50%;
    background: var(--azure);
  }
  .brand__name { font-size: 30px; letter-spacing: 1px; line-height: 1; text-transform: uppercase; }
  .brand__sub { font-size: 11px; letter-spacing: 4px; line-height: 1; margin-top: 6px; text-transform: uppercase; }
  .card--front .brand { left: 0; right: 0; top: 72px; }
  .card--back .brand { left: 250px; width: 216px; top: 52px; }
  .card--back .brand__name { font-size: 26px; }
  .card--back .brand__sub { font-size: 10px; }

  .wave-band {
    position: absolute;
    left: 0; right: 0; bottom: 0;
    background: linear-gradient(to top, var(--royal) 0%, var(--azure) 45%, rgba(51,166,215,0.35) 85%, rgba(51,166,215,0) 100%);
  }
  .card--front .wave-band { height: 38px; }
  .card--back .wave-band { height: 62px; }

  .person { position: absolute; left: 24px; top: 42px; }
  .person__name { font-size: 20px; font-weight: 700; color: var(--royal); line-height: 1.1; }
  .person__role { font-size: 12px; color: var(--ink); margin-top: 6px; }

  .contact { position: absolute; left: 24px; top: 166px; list-style: none; }
  .contact__item {
    display: flex; align-items: center; gap: 9px;
    font-size: 13px; color: var(--ink); height: 19px;
  }
  .contact__icon { width: 11px; height: 11px; fill: var(--navy); flex: none; }
</style>
</head>
<body>

<section class="card card--front" aria-label="Card front">
  <div class="brand">
    <span class="brand__mark"></span>
    <div class="brand__name">Tidecrest</div>
    <div class="brand__sub">Event Group</div>
  </div>
  <div class="wave-band" role="img" aria-label="Row of blue sound-wave equalizer bars along the bottom edge"></div>
</section>

<section class="card card--back" aria-label="Card back">
  <div class="person">
    <div class="person__name">Mara Ellison</div>
    <div class="person__role">Founder &amp; CEO</div>
  </div>

  <div class="brand">
    <span class="brand__mark"></span>
    <div class="brand__name">Tidecrest</div>
    <div class="brand__sub">Event Group</div>
  </div>

  <ul class="contact">
    <li class="contact__item">
      <svg class="contact__icon" viewBox="0 0 12 12" aria-hidden="true"><path d="M1 3.5C1 2 2.5 1 6 1s5 1 5 2.5V5H8.5V3.8H3.5V5H1z"/><path d="M2.5 6h7l1 5h-9z"/></svg>
      952 4186 3307
    </li>
    <li class="contact__item">
      <svg class="contact__icon" viewBox="0 0 12 12" aria-hidden="true"><path d="M0.5 2.5h11v7h-11z M1.5 3.3l4.5 3.3 4.5-3.3" fill="none" stroke="var(--navy)" stroke-width="1.2"/><path d="M0.5 2.5h11L6 6.5z"/></svg>
      mara@tidecrest.com
    </li>
    <li class="contact__item">
      <svg class="contact__icon" viewBox="0 0 12 12" aria-hidden="true"><g fill="none" stroke="var(--navy)" stroke-width="1"><circle cx="6" cy="6" r="5"/><ellipse cx="6" cy="6" rx="2.2" ry="5"/><path d="M1 6h10M2 3.3h8M2 8.7h8"/></g></svg>
      www.tidecrest.com
    </li>
  </ul>

  <div class="wave-band" role="img" aria-label="Row of blue sound-wave equalizer bars along the bottom edge"></div>
</section>

</body>
</html>
```